KDWB Business Card

Looking for a business card design to incorporate our branding. We want to only use the colors listing in the Branding Package (attached).
Updates

Target Market(s)

People who need their phone or device fixed.

Industry/Entity Type

Electronics

Contact Information for Business Card

Please use:

Brightwick Gadget Clinic LLC
4810 E Harlow Ridge Rd
Suite 417
San Antonio, TX 78163

Marcus Delgrove, Store Manager

(210) 555-0147

Requirements
Must have
• Must include the colors that are contained within the Branding Package PDF file.

```html
<!DOCTYPE html>
<html lang="en">
<head>
<meta charset="utf-8">
<title>Brightwick Gadget Clinic – Business Card</title>
<link href="https://fonts.googleapis.com/css2?family=Roboto:wght@300;400;500&display=swap" rel="stylesheet">
<style>
  :root {
    --bg: #e8e5e0;
    --card: #ffffff;
    --orange: #e8532a;
    --grey: #58595b;
    --ink: #3d3d3f;
    --rule: #6d6e70;
    --photo-top: #e4e6ea;
    --photo-mid: #aeb9c8;
    --photo-blue: #3f72c6;
  }
  * { margin: 0; padding: 0; box-sizing: border-box; }
  html, body { width: 1200px; height: 902px; overflow: hidden; }
  body {
    background: var(--bg);
    font-family: "Roboto", Arial, sans-serif;
    position: relative;
  }
  .card {
    position: absolute;
    left: 250px;
    width: 700px;
    height: 400px;
    background: var(--card);
    box-shadow: 0 4px 16px rgba(0,0,0,.18);
    overflow: hidden;
  }
  .card--back { top: 30px; }
  .card--front { top: 470px; }

  /* back side */
  .photo-area {
    position: absolute; inset: 0;
    background: linear-gradient(180deg, var(--photo-top) 0%, var(--photo-mid) 45%, var(--photo-blue) 75%, #2f5fb0 100%);
  }
  .logo-band {
    position: absolute; left: 0; right: 0; top: 190px; height: 90px;
    background: rgba(255,255,255,.96);
    display: flex; align-items: center; justify-content: center; gap: 16px;
  }

  /* brand lockup */
  .brand-mark {
    width: 44px; height: 44px; border-radius: 8px;
    background: var(--orange); flex: none;
  }
  .brand-name {
    color: var(--orange);
    font-weight: 400;
    font-size: 28px;
    white-space: nowrap;
  }
  .brand {
    position: absolute; left: 38px; top: 150px;
    display: flex; align-items: center; gap: 14px;
  }
  .brand .brand-name { font-size: 23px; }

  /* front side */
  .divider {
    position: absolute; left: 395px; top: 45px;
    width: 2px; height: 215px; background: var(--rule);
  }
  .contact { position: absolute; left: 420px; top: 45px; }
  .person-name { font-size: 30px; font-weight: 300; color: var(--ink); line-height: 1.1; }
  .person-title { font-size: 15px; color: var(--orange); margin-top: 4px; }
  .contact-list { list-style: none; margin-top: 28px; }
  .contact-list li {
    display: flex; align-items: center; gap: 10px;
    font-size: 15px; line-height: 18px; color: var(--ink); font-weight: 400;
    margin-bottom: 9px;
  }
  .contact-list li.gap { margin-bottom: 24px; }
  .contact-icon { width: 16px; height: 16px; flex: none; }
  .swoosh { position: absolute; inset: 0; }
  .address { fill: #ffffff; font-size: 14px; font-family: "Roboto", Arial, sans-serif; }
</style>
</head>
<body>

<section class="card card--back" aria-label="Card back">
  <div class="photo-area" role="img" aria-label="Photo of hands repairing a smartphone on a blue work mat"></div>
  <div class="logo-band">
    <span class="brand-mark"></span>
    <span class="brand-name">Brightwick Gadget Clinic</span>
  </div>
</section>

<section class="card card--front" aria-label="Card front">
  <svg class="swoosh" width="700" height="400" viewBox="0 0 700 400">
    <path d="M0 330 C260 322 480 292 700 240 L700 248 C480 304 260 340 0 352 Z" fill="var(--orange)"/>
    <path d="M0 362 C260 350 480 312 700 256 L700 400 L0 400 Z" fill="var(--grey)"/>
    <path id="address-path" d="M150 390 C330 370 500 338 680 285" fill="none"/>
    <text class="address"><textPath href="#address-path">4810 E Harlow Ridge Rd, Suite 417, San Antonio, TX 78163</textPath></text>
  </svg>

  <div class="brand">
    <span class="brand-mark"></span>
    <span class="brand-name">Brightwick Gadget Clinic</span>
  </div>

  <div class="divider"></div>

  <div class="contact">
    <div class="person-name">Marcus Delgrove</div>
    <div class="person-title">Store Manager</div>
    <ul class="contact-list">
      <li class="gap">
        <svg class="contact-icon" viewBox="0 0 16 16"><rect width="16" height="16" rx="2" fill="var(--orange)"/><path d="M5 3.5 L7 6 L6 7.2 C6.8 8.8 7.6 9.6 9 10.2 L10.2 9 L12.5 11 L11.3 12.6 C7.5 12.2 4 8.6 3.6 4.7 Z" fill="#fff"/></svg>
        (210) 555-0147
      </li>
      <li>
        <svg class="contact-icon" viewBox="0 0 16 16"><rect width="16" height="16" rx="2" fill="var(--orange)"/><rect x="3.5" y="5" width="9" height="6.5" fill="#fff"/><path d="M3.5 5 L8 8.8 L12.5 5" fill="none" stroke="var(--orange)" stroke-width="1.2"/></svg>
        marcus@brightwickclinic.com
      </li>
      <li>
        <svg class="contact-icon" viewBox="0 0 16 16"><rect width="16" height="16" rx="2" fill="var(--orange)"/><circle cx="8" cy="8" r="4.5" fill="none" stroke="#fff" stroke-width="1.4"/><path d="M3.5 8 H12.5 M8 3.5 V12.5" stroke="#fff" stroke-width="1"/></svg>
        www.brightwickclinic.com
      </li>
    </ul>
  </div>
</section>

</body>
</html>
```